Loom Harbor needs a website

I sell rugs and carpet on my website, loomharborfloors.example. I need help with the site design to make it "pop". The logo in the header has been designed and I want the site to match it's style and color. Also I have some example sites for layout:
matsquick.example
weave-outlet.example

Industry/Entity Type

Carpet

Requirements
Must have
• Scrolling images on front page. I will insert photos, just need the code.

```html
<!DOCTYPE html>
<html lang="en">
<head>
<meta charset="utf-8">
<title>Loom Harbor – Rugs &amp; Carpet</title>
<link rel="stylesheet" href="https://fonts.googleapis.com/css2?family=Open+Sans:wght@400;600;700&family=Oswald:wght@400;500;700&display=swap">
<style>
:root{
  --green:#6aaa45;
  --green-dark:#4f8a31;
  --navy:#1d3a6b;
  --ink:#333;
  --muted:#777;
  --line:#dcdcdc;
  --panel:#f1f1f1;
  --footer:#e8e8e8;
  --red:#c0392b;
}
*{box-sizing:border-box;margin:0;padding:0}
html,body{width:761px;height:1200px;overflow:hidden;background:#fff}
body{position:relative;font-family:"Open Sans",Arial,sans-serif;color:var(--ink);font-size:8px}
.abs{position:absolute}

/* header */
.brand{left:63px;top:24px;display:flex;align-items:center;gap:8px}
.brand-dot{width:34px;height:34px;border-radius:50%;background:var(--navy)}
.brand-name{font-family:"Open Sans",sans-serif;font-weight:700;font-size:24px;color:var(--green);letter-spacing:-.5px}
.util{right:63px;top:12px;text-align:right;font-size:7.5px;line-height:14px;color:var(--ink)}
.search{right:63px;top:46px;display:flex;align-items:center;gap:5px}
.search input{width:120px;height:15px;border:1px solid var(--line);font-size:7px;padding:0 4px}
.search .go{width:16px;height:15px;background:var(--navy)}
.search .login{font-size:7px;color:var(--ink)}
.search .cart{width:15px;height:15px;background:var(--green)}

/* nav */
.nav{left:63px;top:74px;width:635px;height:22px;background:var(--green);display:flex}
.nav a{color:#fff;text-decoration:none;font-size:7.5px;font-weight:700;display:flex;align-items:center;padding:0 24px;letter-spacing:.3px}
.nav a.active{background:var(--navy)}

/* hero */
.hero{left:63px;top:107px;width:470px;height:253px;background:linear-gradient(135deg,#efe6d6 0%,#d8c3a1 45%,#b99873 75%,#8a6c4d 100%)}
.dots{left:268px;top:344px;display:flex;gap:5px}
.dots span{width:6px;height:6px;border-radius:50%;background:#fff;opacity:.7}
.dots span.on{background:var(--green);opacity:1}
.sale{left:541px;top:107px;width:157px;height:253px;background:var(--navy);color:#fff;text-align:center;font-family:"Oswald",sans-serif;padding-top:26px}
.sale .s1{font-size:46px;font-weight:500;line-height:48px}
.sale .s2{font-size:17px;line-height:20px;margin-top:4px}
.sale .s3{font-size:62px;font-weight:700;line-height:64px}
.sale .s3 small{font-size:28px;vertical-align:top;line-height:40px}
.sale .s4{font-size:34px;line-height:34px}
.sale .btn{display:inline-block;margin-top:10px;background:#fff;color:var(--navy);font-family:"Open Sans",sans-serif;font-size:7px;font-weight:700;padding:3px 8px}

/* promo row */
.promo-new{left:63px;top:373px;width:153px;height:217px;background:var(--green)}
.promo-new .ph{height:110px;background:linear-gradient(160deg,#c9c6bf,#8f8a80)}
.promo-new h3{font-family:"Oswald",sans-serif;color:#fff;font-weight:500;font-size:34px;line-height:36px;padding:14px 12px 0}
.promo-tile{left:229px;top:373px;width:152px;height:217px;border:1px solid var(--line);text-align:center}
.promo-tile .ph{height:110px;background:linear-gradient(180deg,#e9e6e1,#b9b3aa)}
.promo-tile h3{font-family:"Oswald",sans-serif;font-size:15px;font-weight:500;margin-top:14px;color:var(--ink)}
.promo-tile p{font-size:6.5px;line-height:9px;color:var(--muted);padding:6px 16px 0}
.promo-tile a{display:block;margin-top:10px;color:var(--red);font-size:7px;font-weight:600}
.promo-nature{left:394px;top:373px;width:304px;height:217px;background:linear-gradient(180deg,#f3f2ee 0%,#e0ddd5 55%,#8d8a82 100%)}
.promo-nature h3{position:absolute;left:40px;top:28px;font-family:"Oswald",sans-serif;font-weight:500;line-height:1}
.promo-nature .t1{font-size:16px;color:var(--green)}
.promo-nature .t2{font-size:28px;color:var(--green-dark);margin-top:3px}
.rule{left:63px;top:610px;width:635px;height:1px;background:var(--line)}

/* sidebar */
.cats{left:63px;top:630px;width:161px;border:1px solid var(--line);background:var(--panel)}
.cats h4{background:var(--green);color:#fff;font-size:9px;font-weight:700;padding:6px 10px}
.cats li{list-style:none;font-size:7px;padding:0 10px 0 14px;height:21px;line-height:21px;border-top:1px solid #e2e2e2;position:relative}
.cats li::before{content:"";position:absolute;left:7px;top:9px;width:3px;height:3px;background:var(--green)}
.freeship{left:63px;top:894px;width:161px;height:147px;background:linear-gradient(150deg,#8d8b86 0%,#5d5a55 60%,#3c3a37 100%);color:#fff;font-family:"Oswald",sans-serif;padding:16px 12px}
.freeship .f1{font-size:30px;font-weight:700;line-height:30px}
.freeship .f2{font-size:30px;font-weight:700;line-height:30px}
.freeship .f3{font-size:11px;margin-top:4px}
.freeship .f4{font-size:30px;font-weight:700;line-height:32px}

/* products */
.product{width:140px}
.product .ph{height:105px;border:5px solid #eee}
.product .name{color:var(--green);font-weight:700;font-size:7px;margin-top:6px}
.product .desc{font-size:6.5px;color:var(--muted)}
.product .price{font-size:7px;font-weight:700;margin-top:2px}
.product .acts{display:flex;gap:4px;margin-top:5px}
.product .add{background:var(--green);color:#fff;font-size:6.5px;font-weight:700;padding:4px 7px}
.product .view{background:var(--navy);color:#fff;font-size:6.5px;font-weight:700;padding:4px 7px}
.r1 .ph{background:linear-gradient(135deg,#dcbf86,#b8904f)}
.r2 .ph{background:linear-gradient(135deg,#8a8570,#4d4b3f)}
.r3 .ph{background:linear-gradient(135deg,#e0c796,#c4a56b)}
.r4 .ph{background:linear-gradient(135deg,#a09d88,#5f6b66)}

/* follow */
.follow{right:63px;top:1041px;display:flex;align-items:center;gap:6px}
.follow b{font-size:9px;font-weight:700;color:var(--navy);margin-right:4px}
.follow span{width:14px;height:14px;border-radius:50%;background:#9aa3ad}

/* footer */
.footer{left:0;top:1080px;width:761px;height:120px;background:var(--footer)}
.fcol{top:12px}
.fcol h5{font-size:8px;font-weight:700;color:var(--ink);margin-bottom:6px}
.fcol li{list-style:none;font-size:6.5px;color:var(--muted);line-height:10px}
.news{display:flex;margin-top:2px}
.news input{width:110px;height:16px;border:1px solid var(--line);font-size:6.5px;padding:0 4px}
.news .go{width:18px;height:16px;background:var(--green)}
.copy{left:0;bottom:0;width:761px;height:18px;line-height:18px;background:#dcdcdc;text-align:right;padding-right:63px;font-size:6.5px;color:var(--muted)}
</style>
</head>
<body>

<header>
  <div class="abs brand"><span class="brand-dot"></span><span class="brand-name">Loom Harbor</span></div>
  <div class="abs util">Items: 0 | Total: $0.00 Cart | Checkout<br>Order toll free: 555-010-2040</div>
  <div class="abs search"><input type="text" placeholder="Search"><span class="go"></span><span class="login">Login</span><span class="cart"></span></div>
  <nav class="abs nav">
    <a class="active" href="#">HOME</a><a href="#">ABOUT US</a><a href="#">CONTACT US</a><a href="#">MY ACCOUNT</a><a href="#">VIEW CART/CHECKOUT</a>
  </nav>
</header>

<section>
  <div class="abs hero" role="img" aria-label="Slideshow photo of rolled rugs and carpets"></div>
  <div class="abs dots"><span class="on"></span><span></span><span></span></div>
  <div class="abs sale">
    <div class="s1">SALE</div>
    <div class="s2">GET UP TO</div>
    <div class="s3">50<small>%</small></div>
    <div class="s4">OFF</div>
    <span class="btn">SHOP NOW</span>
  </div>
</section>

<section>
  <div class="abs promo-new">
    <div class="ph" role="img" aria-label="Photo of a room with a new rug"></div>
    <h3>NEW<br>ARRIVALS</h3>
  </div>
  <div class="abs promo-tile">
    <div class="ph" role="img" aria-label="Photo of ceramic floor tiles"></div>
    <h3>CERAMIC TILES</h3>
    <p>Durable glazed tiles for every room, easy to clean and built to last for years.</p>
    <a>Shop now</a>
  </div>
  <div class="abs promo-nature" role="img" aria-label="Photo of a living room with a natural rug">
    <h3><div class="t1">BRING A TOUCH OF</div><div class="t2">NATURE HOME!</div></h3>
  </div>
  <div class="abs rule"></div>
</section>

<aside>
  <div class="abs cats">
    <h4>Shop by Category</h4>
    <ul>
      <li>Commercial Flooring</li><li>Carpet Flooring</li><li>Commercial Flooring</li><li>Carpet Flooring</li><li>Hardwood Flooring</li>
      <li>Area Rugs</li><li>Commercial Flooring</li><li>Carpet Flooring</li><li>Area Rugs</li><li>Commercial Flooring</li>
    </ul>
  </div>
  <div class="abs freeship" role="img" aria-label="Photo of a carpeted room behind free shipping offer">
    <div class="f1">FREE</div><div class="f2">SHIPPING</div><div class="f3">ON ORDERS OVER</div><div class="f4">$499</div>
  </div>
</aside>

<main>
  <div class="abs product r1" style="left:246px;top:630px"><div class="ph" role="img" aria-label="Rug swatch"></div><div class="name">CANADIAN MAPLE</div><div class="desc">8' x 10' Wool Blend</div><div class="price">Price: $9.39</div><div class="acts"><span class="add">ADD TO CART</span><span class="view">VIEW</span></div></div>
  <div class="abs product r2" style="left:402px;top:630px"><div class="ph" role="img" aria-label="Rug swatch"></div><div class="name">CANADIAN MAPLE</div><div class="desc">8' x 10' Wool Blend</div><div class="price">Price: $9.39</div><div class="acts"><span class="add">ADD TO CART</span><span class="view">VIEW</span></div></div>
  <div class="abs product r3" style="left:558px;top:630px"><div class="ph" role="img" aria-label="Rug swatch"></div><div class="name">CANADIAN MAPLE</div><div class="desc">8' x 10' Wool Blend</div><div class="price">Price: $9.39</div><div class="acts"><span class="add">ADD TO CART</span><span class="view">VIEW</span></div></div>
  <div class="abs product r3" style="left:246px;top:838px"><div class="ph" role="img" aria-label="Rug swatch"></div><div class="name">CANADIAN MAPLE</div><div class="desc">8' x 10' Wool Blend</div><div class="price">Price: $9.39</div><div class="acts"><span class="add">ADD TO CART</span><span class="view">VIEW</span></div></div>
  <div class="abs product r4" style="left:402px;top:838px"><div class="ph" role="img" aria-label="Rug swatch"></div><div class="name">CANADIAN MAPLE</div><div class="desc">8' x 10' Wool Blend</div><div class="price">Price: $9.39</div><div class="acts"><span class="add">ADD TO CART</span><span class="view">VIEW</span></div></div>
  <div class="abs product r1" style="left:558px;top:838px"><div class="ph" role="img" aria-label="Rug swatch"></div><div class="name">CANADIAN MAPLE</div><div class="desc">8' x 10' Wool Blend</div><div class="price">Price: $9.39</div><div class="acts"><span class="add">ADD TO CART</span><span class="view">VIEW</span></div></div>
  <div class="abs follow"><b>FOLLOW US</b><span></span><span></span><span></span></div>
</main>

<footer class="abs footer">
  <div class="abs fcol" style="left:63px"><h5>INFORMATION</h5><ul><li>About Us</li><li>Customer Service</li><li>Privacy Policy</li><li>Site Map</li></ul></div>
  <div class="abs fcol" style="left:205px"><h5>WHY BUY FROM US</h5><ul><li>Shipping &amp; Returns</li><li>Secure Shopping</li><li>International Shipping</li><li>Affiliates</li></ul></div>
  <div class="abs fcol" style="left:345px"><h5>MY ACCOUNT</h5><ul><li>Sign In</li><li>View Cart</li><li>My Wishlist</li><li>Track My Order</li></ul></div>
  <div class="abs fcol" style="left:490px"><h5>NEWSLETTER</h5><div class="news"><input type="text" placeholder="Enter your email"><span class="go"></span></div></div>
  <div class="abs copy">© Copyright Loom Harbor 2014, All Rights Reserved</div>
</footer>

</body>
</html>
```